Brochure for a website accessibility report

This brochure is related to a report that www.qelvantrix.org sell. The report shows the results of an automated audit of a websites accessibility. It shows details of issues found with screen shots, examples of code and provides remediation advice.

The brochure will be a pdf 8.5 inches by 11 inches. It can be anywhere from 6 to 10 pages.

The FlintVue™ name itself should be “Bree Serif” font. The fonts, styles, colors and sizes are up to you.

The images used and logo of the Office of Digital Reachworks and K7P logo are upload

We highlighted in blue page extracts from the report we sell. Do not use the blue highlight, it is merely there to show you where the specific examples of the report we sell are vs the other content in the report. The areas in blue which show the content from the actual report should be shown as an extract of the actual page of the report. You have flexibility to change the layout and the way the content look.

The red square callouts over the blue content are callouts that describe the specific page extracts. We used it as a red callout only so that you would be able to see it. You should change the specific location, look and feel of the callout to be appropriate

Target Market(s)

Marketing and Technical people

Industry/Entity Type

Information Technology

Font styles to use
Sans Serif

Colors

Designer to choose colors to be used in the design.

Requirements
Should not have
• wheelchairs, images of blind people

```html
<!DOCTYPE html>
<html lang="en">
<head>
<meta charset="utf-8">
<title>Office of Digital Reachworks – FlintVue™ Brochure Covers</title>
<link rel="stylesheet" href="https://fonts.googleapis.com/css2?family=Lato:wght@400;700;900&family=Bree+Serif&display=swap">
<style>
  :root {
    --bg: #e4e4e4;
    --paper: #f3f3f4;
    --paper-white: #fafafa;
    --green: #00854a;
    --green-light: #2fa36c;
    --green-deep: #0a6b3e;
    --accent: #2aa36b;
    --ink: #1b1b1b;
    --body: #3c3c3c;
    --rule: #141414;
  }
  * { box-sizing: border-box; margin: 0; padding: 0; }
  html, body { width: 1200px; height: 824px; overflow: hidden; }
  body {
    background: var(--bg);
    font-family: "Lato", Arial, sans-serif;
    position: relative;
  }
  .spread {
    position: absolute;
    left: 40px; top: 50px;
    width: 1120px; height: 724px;
    display: flex;
    box-shadow: 0 6px 24px rgba(0,0,0,.18);
  }
  .page {
    position: relative;
    width: 560px; height: 724px;
    background: var(--paper);
    overflow: hidden;
  }
  .page-art { position: absolute; inset: 0; width: 560px; height: 724px; }

  /* Back cover */
  .back-headline {
    position: absolute; left: 50px; top: 200px; width: 440px;
    color: var(--accent); font-weight: 900; font-size: 23px; line-height: 1.2;
  }
  .back-headline .product { font-family: "Bree Serif", Georgia, serif; font-weight: 400; }
  .back-copy {
    position: absolute; left: 50px; top: 272px; width: 410px;
    color: var(--body); font-size: 11.5px; line-height: 1.45;
  }
  .back-copy p + p { margin-top: 9px; }
  .back-copy .product { font-family: "Bree Serif", Georgia, serif; }

  .brand-block {
    position: absolute; display: flex; align-items: center; gap: 16px;
  }
  .brand-mark { width: 34px; height: 34px; flex: none; }
  .brand-name {
    font-family: "Lato", Arial, sans-serif; font-weight: 900;
    text-transform: uppercase; letter-spacing: .5px; line-height: 1.05;
  }
  .brand-block--back { left: 90px; top: 505px; }
  .brand-block--back .brand-mark { background: var(--paper-white); }
  .brand-block--back .brand-name { color: var(--paper-white); font-size: 28px; }
  .back-contact {
    position: absolute; left: 140px; top: 602px;
    color: var(--paper-white); font-weight: 700; font-size: 18px; line-height: 1.25;
  }

  /* Front cover */
  .front-title-card {
    position: absolute; left: 50px; top: 110px; width: 410px; height: 220px;
    background: var(--paper); display: flex; align-items: center; justify-content: center;
  }
  .brand-block--front { position: static; }
  .brand-block--front .brand-mark { background: var(--green-light); }
  .brand-block--front .brand-name { color: var(--ink); font-size: 28px; }
</style>
</head>
<body>
<main class="spread">

  <section class="page page--back" aria-label="Back cover">
    <svg class="page-art" viewBox="0 0 560 724">
      <defs>
        <linearGradient id="swoosh" x1="0" y1="1" x2="1" y2="0">
          <stop offset="0" stop-color="#e8ecb8"/>
          <stop offset=".55" stop-color="#b9d7a0"/>
          <stop offset="1" stop-color="#7fb39a"/>
        </linearGradient>
        <linearGradient id="teamBack" x1="0" y1="0" x2="1" y2="1">
          <stop offset="0" stop-color="#1e9d63"/>
          <stop offset=".6" stop-color="#0b8249"/>
          <stop offset="1" stop-color="#066c3b"/>
        </linearGradient>
      </defs>
      <path role="img" aria-label="Soft decorative wave in green and yellow" d="M0,170 Q300,140 560,0 L560,110 Q300,150 0,190 Z" fill="url(#swoosh)" opacity=".75"/>
      <path role="img" aria-label="Green tinted photo of a team working at laptops" d="M0,490 Q330,460 560,400 L560,665 L0,665 Z" fill="url(#teamBack)"/>
      <path d="M0,490 Q330,460 560,400" fill="none" stroke="var(--rule)" stroke-width="5"/>
      <rect x="0" y="665" width="560" height="59" fill="var(--paper-white)"/>
    </svg>

    <h2 class="back-headline">Start your journey to a fully compliant website with <span class="product">FlintVue™</span> today.</h2>
    <div class="back-copy">
      <p>Your complete <span class="product">FlintVue™</span> report, including both the WCAG 2.1 A/AA website compliance results and the detailed website developer guide, is only $850.</p>
      <p>Ready to get started? Act now to receive all of this detailed information and help ensure you aren’t in violation of civil rights laws and in danger of potential lawsuits.</p>
      <p>Order your <span class="product">FlintVue™</span> report right now at https://www.qelvantrix.org/FlintVue/. For more information or to speak with one of our Customer Success Representatives, email or call us today.</p>
    </div>

    <div class="brand-block brand-block--back">
      <span class="brand-mark"></span>
      <span class="brand-name">Office of<br>Digital<br>Reachworks</span>
    </div>
    <p class="back-contact">Contact@qelvantrix.org<br>555.204.7318</p>
  </section>

  <section class="page page--front" aria-label="Front cover">
    <svg class="page-art" viewBox="0 0 560 724">
      <defs>
        <linearGradient id="circuit" x1="0" y1="0" x2="1" y2="1">
          <stop offset="0" stop-color="#5d5e60"/>
          <stop offset=".5" stop-color="#7a7b7d"/>
          <stop offset="1" stop-color="#646567"/>
        </linearGradient>
        <linearGradient id="teamFront" x1="0" y1="0" x2="1" y2="1">
          <stop offset="0" stop-color="#0d6a3d"/>
          <stop offset=".45" stop-color="#2c9e68"/>
          <stop offset="1" stop-color="#0a7a44"/>
        </linearGradient>
      </defs>
      <rect role="img" aria-label="Grey technology background with circuit lines and a security shield" x="240" y="0" width="320" height="370" fill="url(#circuit)"/>
      <path role="img" aria-label="Green tinted photo of colleagues reviewing documents around laptops" d="M0,400 Q280,350 560,340 L560,665 L0,665 Z" fill="url(#teamFront)"/>
      <path d="M0,400 Q280,350 560,340" fill="none" stroke="var(--rule)" stroke-width="5"/>
      <rect x="0" y="665" width="560" height="59" fill="var(--paper-white)"/>
    </svg>

    <div class="front-title-card">
      <div class="brand-block brand-block--front">
        <span class="brand-mark"></span>
        <span class="brand-name">Office of<br>Digital<br>Reachworks</span>
      </div>
    </div>
  </section>

</main>
</body>
</html>
```